KORVEL Group Pty Ltd. Website and Domain

www.korvelgroup.com.au

require email addresses setup.

Info@korvelgroup.com.au
accounts@korvelgroup.com.au
peter.halloway@korvelgroup.com.au
grant.whitley@korvelgroup.com.au

Website should promote commercial and domestic electrical services, audio visual services and data and fibre installations.

similar to my mates site www.brisvane.com.au

Website needs to promote professionalism, electrical/electrician, audio visual and data/fibre cabling installations.

promote environmental friendly imaginary.

Coding

```html
<!DOCTYPE html>
<html lang="en">
<head>
<meta charset="utf-8">
<title>KORVEL — Electrical . Audio Visual . Data</title>
<link href="https://fonts.googleapis.com/css2?family=Roboto:wght@400;500;700&display=swap" rel="stylesheet">
<style>
:root{
  --green:#a6c93a;
  --blue:#2fa3d8;
  --dark:#111214;
  --panel:#2a2a2b;
  --night:#0c0f16;
  --footer:#1d1d1f;
  --white:#ffffff;
  --muted:#d6d6d6;
}
*{margin:0;padding:0;box-sizing:border-box}
html,body{width:1200px;height:4361px;overflow:hidden}
body{position:relative;background:var(--dark);font-family:'Roboto',Arial,sans-serif;color:var(--white)}
.abs{position:absolute}
.btn{position:absolute;background:var(--green);color:var(--white);font-weight:700;font-size:16px;letter-spacing:1px;display:flex;align-items:center;justify-content:center;text-transform:uppercase}
.brand{position:absolute;display:flex;align-items:center;gap:14px}
.brand-dot{width:62px;height:62px;border-radius:50%;background:var(--blue)}
.brand-name{font-size:46px;font-weight:700;color:var(--blue);letter-spacing:2px}
.sec-title{position:absolute;left:0;width:1200px;display:flex;justify-content:center;align-items:center;gap:14px;font-weight:700;letter-spacing:3px}
.sec-dot{width:64px;height:64px;border-radius:50%;border:5px solid var(--white);background:transparent}
.photo{position:absolute}

/* hero */
.welcome{top:559px;left:0;width:1200px;height:700px;background:linear-gradient(180deg,#05070b 0%,#0f1520 55%,#1a2433 100%)}
.hero{top:0;left:0;width:1200px;height:643px;clip-path:polygon(0 0,100% 0,100% 559px,50% 643px,0 559px);background:var(--night)}
.hero-photo{left:533px;top:0;width:667px;height:643px;background:radial-gradient(ellipse at 55% 40%,#6a4a3a 0%,#2d3a55 40%,#141826 80%)}
.hero-panel{left:0;top:0;width:533px;height:643px;background:var(--panel)}
.menu{left:814px;top:52px;font-size:17px;letter-spacing:2px;color:var(--muted)}
.hero-title{left:88px;top:212px;font-size:62px;font-weight:700;letter-spacing:9px}
.hero-sub{left:88px;top:292px;font-size:29px;font-weight:700;letter-spacing:1px}
.para{position:absolute;font-size:16.5px;line-height:32px;color:var(--muted)}

/* what we do */
.services{top:1120px;left:0;width:1200px;height:561px;background:var(--blue);clip-path:polygon(0 73px,50% 0,100% 73px,100% 100%,0 100%)}
.svc-label{position:absolute;top:1547px;width:200px;font-size:18px;line-height:23px;font-weight:500}

/* who we are */
.kicker{position:absolute;font-size:27px;font-weight:700;color:var(--blue);letter-spacing:1px}
.headline{position:absolute;font-size:32px;font-weight:700;letter-spacing:2px}
.body-copy{position:absolute;font-size:16.5px;line-height:31.5px;color:var(--muted);text-align:justify}
.framed{position:absolute;box-shadow:10px 10px 0 var(--green)}

/* gallery */
.gallery{top:2784px;left:0;width:1200px;height:791px;background:var(--green);clip-path:polygon(0 0,100% 0,100% 703px,50% 791px,0 703px)}

/* contact */
.contact{top:3487px;left:0;width:1200px;height:626px;background:linear-gradient(180deg,#15171b 0%,#1f2227 50%,#141518 100%)}
.field{position:absolute;border:1px solid #cfcfcf;font-size:16px;font-weight:500;padding:12px 16px;color:var(--white)}
.footer{top:4113px;left:0;width:1200px;height:248px;background:var(--footer)}
.info-line{position:absolute;left:0;width:1200px;top:4262px;text-align:center;font-size:16px;display:flex;justify-content:center;align-items:center;gap:8px}
.copy{position:absolute;left:0;width:1200px;top:4303px;text-align:center;font-size:13px}
</style>
</head>
<body>

<!-- welcome band -->
<section class="abs welcome"></section>

<!-- hero -->
<header class="abs hero">
  <div class="photo hero-photo" role="img" aria-label="Close-up of stripped copper electrical cables with blue, green and brown insulation"></div>
  <div class="photo hero-panel"></div>
</header>
<div class="brand" style="left:90px;top:24px">
  <div class="brand-dot" style="width:54px;height:54px"></div>
  <div class="brand-name">KORVEL</div>
</div>
<div class="abs menu">MENU ⌄</div>
<h1 class="abs hero-title">KORVEL</h1>
<div class="abs hero-sub">ELECTRICAL . AUDIO VISUAL . DATA</div>
<div class="btn" style="left:90px;top:367px;width:174px;height:42px">Get Started</div>
<svg class="abs" style="left:588px;top:608px" width="24" height="24" viewBox="0 0 24 24" fill="none" stroke="#ffffff" stroke-width="2"><path d="M5 5l7 7 7-7M5 12l7 7 7-7"/></svg>

<div class="sec-title" style="top:738px;font-size:40px"><div class="sec-dot" style="border-color:var(--green)"></div>WELCOME TO KORVEL</div>
<p class="para" style="left:140px;top:847px;width:920px;text-align:center">Lorem ipsum dolor sit amet, consectetur adipiscing elit, sed do eiusmod tempor incididunt ut labore et dolore magna aliqua. Ut enim ad minim veniam, quis nostrud exercitation ullamco laboris nisi ut aliquip ex ea commodo consequat. Duis aute irure dolor in reprehenderit in voluptate velit esse cillum dolore eu fugiat nulla pariatur.</p>
<div class="btn" style="left:513px;top:978px;width:174px;height:42px">Read More</div>

<!-- what we do -->
<section class="abs services"></section>
<div class="sec-title" style="top:1203px;font-size:40px"><div class="sec-dot"></div>WHAT WE DO</div>
<div class="photo" style="left:90px;top:1313px;width:198px;height:222px;background:linear-gradient(160deg,#c9ccd2,#3457a6)" role="img" aria-label="Trainer guiding apprentices in blue overalls using a multimeter"></div>
<div class="photo" style="left:295px;top:1313px;width:198px;height:222px;background:linear-gradient(160deg,#3a2e28,#2e4f9a)" role="img" aria-label="Hand working on wiring inside a switchboard"></div>
<div class="photo" style="left:501px;top:1313px;width:198px;height:222px;background:linear-gradient(160deg,#1a2a55,#7f9bd6)" role="img" aria-label="Microphone resting on an audio mixing console"></div>
<div class="photo" style="left:707px;top:1313px;width:198px;height:222px;background:linear-gradient(160deg,#e8e2a0,#5ab06d 50%,#c24fc0)" role="img" aria-label="Bundle of colourful fibre optic cables"></div>
<div class="photo" style="left:912px;top:1313px;width:198px;height:222px;background:linear-gradient(160deg,#d8d8d8,#8a9a55)" role="img" aria-label="Electrician in hard hat working at a panel"></div>
<div class="svc-label" style="left:88px">Promote<br>Professionalism</div>
<div class="svc-label" style="left:294px">Electrical/<br>electrician</div>
<div class="svc-label" style="left:500px">Audio Visual</div>
<div class="svc-label" style="left:705px">Data/fibre Cabling<br>Installations</div>
<div class="svc-label" style="left:911px">Promote Environmentally<br>Friendly Imagery</div>

<!-- who we are -->
<div class="sec-title" style="top:1746px;font-size:40px"><div class="sec-dot" style="border-color:var(--green)"></div>WHO WE ARE</div>
<div class="framed" style="left:90px;top:1868px;width:428px;height:359px;background:linear-gradient(90deg,#2e3136 0%,#6e6a66 45%,#e4dfdb 100%)" role="img" aria-label="Technician holding a refrigerant manifold gauge set with red hoses"></div>
<div class="kicker" style="left:570px;top:1876px">COMMERCIAL</div>
<div class="headline" style="left:570px;top:1911px">ELECTRICAL SERVICES</div>
<p class="body-copy" style="left:570px;top:1976px;width:540px">Lorem ipsum dolor sit amet, consectetur adipiscing elit, sed do eiusmod tempor incididunt ut labore et dolore magna aliqua. Ut enim ad minim veniam, quis nostrud exercitation ullamco laboris nisi ut aliquip ex ea commodo consequat. Duis aute irure dolor in reprehenderit in voluptate velit esse cillum dolore eu fugiat nulla pariatur.</p>
<div class="btn" style="left:572px;top:2173px;width:172px;height:42px">Read More</div>

<div class="kicker" style="left:88px;top:2333px">DOMESTIC</div>
<div class="headline" style="left:88px;top:2368px">ELECTRICAL SERVICES</div>
<p class="body-copy" style="left:88px;top:2433px;width:540px">Lorem ipsum dolor sit amet, consectetur adipiscing elit, sed do eiusmod tempor incididunt ut labore et dolore magna aliqua. Ut enim ad minim veniam, quis nostrud exercitation ullamco laboris nisi ut aliquip ex ea commodo consequat. Duis aute irure dolor in reprehenderit in voluptate velit esse cillum dolore eu fugiat nulla pariatur.</p>
<div class="btn" style="left:90px;top:2630px;width:172px;height:42px">Read More</div>
<div class="framed" style="left:672px;top:2326px;width:428px;height:359px;background:linear-gradient(150deg,#5a7db8,#2c4f8e 60%,#c9cfd8)" role="img" aria-label="Hands stripping wires with pliers at an electrical box"></div>

<!-- gallery -->
<section class="abs gallery"></section>
<div class="sec-title" style="top:2847px;font-size:44px"><div class="sec-dot"></div>PROJECT GALLERY</div>
<div class="photo" style="left:156px;top:2953px;width:214px;height:229px;background:linear-gradient(150deg,#2f3a4d,#4d8fc9)" role="img" aria-label="Woman editing video at a computer workstation"></div>
<div class="photo" style="left:382px;top:2953px;width:214px;height:229px;background:linear-gradient(150deg,#d9dde3,#3a4c8c 60%,#e0b22b)" role="img" aria-label="Multimeter testing circuit breakers"></div>
<div class="photo" style="left:606px;top:2953px;width:214px;height:229px;background:linear-gradient(150deg,#0f1b33,#2d6bb0)" role="img" aria-label="Camera filming a stage with blue screen"></div>
<div class="photo" style="left:831px;top:2953px;width:214px;height:229px;background:linear-gradient(150deg,#e6e6e6,#3a3a3c)" role="img" aria-label="Gloved hands working on a fuse panel"></div>
<div class="photo" style="left:156px;top:3195px;width:214px;height:229px;background:linear-gradient(150deg,#c4c6c9,#8a2c2c 60%,#3b3f45)" role="img" aria-label="Technician in red shirt using a tool"></div>
<div class="photo" style="left:382px;top:3195px;width:214px;height:229px;background:linear-gradient(150deg,#f0ede8,#c89d3a 55%,#7a3b2c)" role="img" aria-label="Electrician in yellow hard hat installing a light fitting"></div>
<div class="photo" style="left:606px;top:3195px;width:214px;height:229px;background:linear-gradient(150deg,#e9eef5,#4a5260 55%,#2f6a9a)" role="img" aria-label="Tool bag with coils of cable on a table"></div>
<div class="photo" style="left:831px;top:3195px;width:214px;height:229px;background:linear-gradient(150deg,#1d3d8a,#e09a2a 60%,#2d2d2d)" role="img" aria-label="Worker holding an orange extension cable reel"></div>

<!-- contact -->
<section class="abs contact"></section>
<section class="abs gallery" style="z-index:0;clip-path:polygon(0 703px,50% 791px,100% 703px,100% 0,0 0);visibility:hidden"></section>
<div class="sec-title" style="top:3640px;font-size:40px"><div class="sec-dot" style="border-color:var(--green)"></div>GET IN TOUCH</div>
<div class="field" style="left:162px;top:3749px;width:434px;height:46px">Name</div>
<div class="field" style="left:604px;top:3749px;width:434px;height:46px">Email</div>
<div class="field" style="left:162px;top:3806px;width:876px;height:98px">Message</div>
<div class="btn" style="left:513px;top:3917px;width:174px;height:45px">Submit</div>

<!-- footer -->
<footer class="abs footer"></footer>
<div class="brand" style="left:462px;top:4160px">
  <div class="brand-dot"></div>
  <div class="brand-name">KORVEL</div>
</div>
<div class="info-line">
  <svg width="14" height="14" viewBox="0 0 24 24" fill="#ffffff"><path d="M6.6 10.8a15 15 0 006.6 6.6l2.2-2.2a1 1 0 011-.25 11.4 11.4 0 003.6.6 1 1 0 011 1V20a1 1 0 01-1 1A17 17 0 013 4a1 1 0 011-1h3.5a1 1 0 011 1c0 1.25.2 2.45.6 3.6a1 1 0 01-.25 1z"/></svg>
  <span>+8 555 010 247</span><span>&nbsp;|&nbsp;</span>
  <svg width="15" height="12" viewBox="0 0 24 18" fill="#ffffff"><path d="M0 0h24v2L12 10 0 2zM0 4l12 8 12-8v14H0z"/></svg>
  <span>info@korvelgroup.com.au</span><span>&nbsp;|&nbsp;</span>
  <svg width="11" height="15" viewBox="0 0 16 22" fill="#ffffff"><path d="M8 0a8 8 0 00-8 8c0 6 8 14 8 14s8-8 8-14a8 8 0 00-8-8zm0 11a3 3 0 110-6 3 3 0 010 6z"/></svg>
  <span>212 Harlow Street,Westbridge,QLD</span>
</div>
<div class="copy">Copyright © 2020.The Company Name. All Rights Reserved.</div>

</body>
</html>
```